Korvath Supply Website Redesign

Currently korvathsupply.example is focussed on fulfillment and transport from various products in the BBQ segment. However, no we want to update our business activities to Product Development, Brand Development, Online Positioning, Logistics & Aftersales, and Promotional BBQs. We will be a business for Outdoor Leisure Development from A to Z.

Therefore, we need a brand new website. The colours of the current website may be the same. However, i'd like to keep it clean. More white and use blue and green as accent colours. It is a business to business organization so the website should be looking formal and corporate. However we sell fun products so not too formal and corporate.

Pages we need; Home, About, Contact, Our Services (+ page per service) a place to share our news/blogs.

I have added some sort of mock up of an idea. However it needs some finetuning.

Target Market(s)

Businesses

Industry/Entity Type

Corporate/Logistics/Marketing

Coding

Coded - Design and coding required

Colors

Designer to choose colors to be used in the design.

Requirements
Must have
• Show clear distinguishing of the different services we provide (Product Development, Brand Development, Online Positioning, Logistics & Aftersales and Promotional BBQs). Every service should have its own page too. Besides, I would like to have a blog page to share relevant content.
Nice to have
• Show that we are the expert in Outdoor LEisure Development from A to Z
Should not have
• Be too informal. It may be semi-formal

```html
<!DOCTYPE html>
<html lang="en">
<head>
<meta charset="utf-8">
<title>Korvath Supply — Home</title>
<link rel="stylesheet" href="https://fonts.googleapis.com/css2?family=Montserrat:wght@400;500;600;700;800;900&display=swap">
<style>
:root{
  --teal:#2c5b6b;
  --teal-dark:#234a58;
  --green:#2f9b3b;
  --green-soft:#36a544;
  --ink:#333b40;
  --muted:#555f64;
  --white:#ffffff;
  --line:#d7dcde;
}
*{box-sizing:border-box;margin:0;padding:0}
html,body{width:1200px;height:2957px;overflow:hidden}
body{position:relative;font-family:"Montserrat",Arial,sans-serif;color:var(--ink);background:var(--white)}
.btn{position:absolute;display:flex;align-items:center;justify-content:center;background:var(--teal);color:var(--white);border-radius:24px;font-weight:600;font-size:15px;letter-spacing:.3px;text-transform:uppercase}
.brand{display:flex;align-items:center;gap:10px;color:var(--teal);font-weight:900;letter-spacing:.5px;white-space:nowrap}
.brand .dot{border-radius:50%;background:var(--green);flex:none}

/* header */
.site-header{position:absolute;left:0;top:0;width:1200px;height:69px;background:var(--white);border-top:3px solid var(--teal)}
.site-header .brand{position:absolute;left:110px;top:8px;height:54px;font-size:36px}
.site-header .brand .dot{width:38px;height:38px}
.nav a{position:absolute;top:27px;font-size:14px;font-weight:500;color:var(--ink);text-decoration:none}
.nav a.active{color:var(--teal)}
.nav a.active::after{content:"";position:absolute;left:0;right:0;top:38px;height:3px;background:var(--teal)}

/* hero */
.hero{position:absolute;left:0;top:69px;width:1200px;height:574px;background:linear-gradient(90deg,#0f2338 0%,#142c45 38%,#5a3a1e 50%,#2d3f5a 62%,#1d2b45 100%)}
.hero h1{position:absolute;left:110px;top:204px;color:var(--white);font-size:44px;font-weight:800;line-height:53px}
.hero .btn{left:112px;top:316px;width:159px;height:45px}
.hero-arrow{position:absolute;top:260px;width:54px;height:54px;border:2px solid var(--white);border-radius:50%}
.hero-dots span{position:absolute;top:524px;width:13px;height:13px;border-radius:50%;border:2px solid var(--white)}
.hero-dots span.on{background:var(--green);border-color:var(--green)}

/* services */
.service{position:absolute;top:730px;width:207px;height:257px;background:var(--white);border-radius:8px;box-shadow:0 2px 10px rgba(0,0,0,.16);text-align:center}
.service svg{position:absolute;left:64px;top:36px}
.service h3{position:absolute;left:0;right:0;top:142px;color:var(--teal);font-size:19px;font-weight:700;line-height:23px}
.service p{position:absolute;left:8px;right:8px;top:198px;font-size:12px;line-height:18px;color:var(--ink)}

/* special */
.special{position:absolute;left:0;top:1072px;width:1200px;height:487px;background:var(--green)}
.special h2{position:absolute;left:110px;top:86px;color:var(--white);font-size:38px;font-weight:800}
.special p{position:absolute;left:110px;top:142px;width:506px;color:var(--white);font-size:16.5px;line-height:27.5px}
.special .btn{left:110px;top:356px;width:160px;height:45px}
.special-photo{position:absolute;left:664px;top:86px;width:459px;height:315px;border-radius:6px;background:linear-gradient(110deg,#b9c7cf 0%,#c05a3c 30%,#2a5e96 55%,#2f7f8c 75%,#d26a2e 100%)}

/* silent */
.silent h2{position:absolute;left:0;width:1200px;top:1640px;text-align:center;color:var(--teal);font-size:39px;font-weight:800}
.silent p{position:absolute;left:150px;width:900px;top:1698px;text-align:center;color:var(--muted);font-size:16.5px;line-height:27.5px}
.silent .btn{left:442px;top:1794px;width:316px;height:46px}

/* contact */
.contact{position:absolute;left:0;top:1926px;width:1200px;height:611px;background:linear-gradient(135deg,#3d3424 0%,#23344a 40%,#1b3550 70%,#2a3a40 100%)}
.contact h2{position:absolute;left:0;width:1200px;top:80px;text-align:center;color:var(--white);font-size:37px;font-weight:800}
.contact .lead{position:absolute;left:230px;width:740px;top:128px;text-align:center;color:var(--white);font-size:16.5px;line-height:27px}
.field{position:absolute;height:46px;background:var(--white);border-radius:4px;display:flex;align-items:center;gap:12px;padding-left:16px;font-size:15px;color:var(--muted)}
.field svg{flex:none}
.field.area{align-items:flex-start;padding-top:14px;height:130px}
.contact .btn{left:442px;top:480px;width:316px;height:46px}

/* footer */
.site-footer .brand{position:absolute;left:142px;top:2666px;height:70px;font-size:40px}
.site-footer .brand .dot{width:46px;height:46px}
.foot-col h4{position:absolute;top:2606px;font-size:20px;font-weight:600;color:var(--teal-dark)}
.foot-col .rule{position:absolute;top:2643px;width:44px;height:3px;background:var(--teal)}
.foot-col li{position:absolute;list-style:none;font-size:13px;font-weight:500;color:var(--ink)}
.foot-contact li{display:flex;align-items:flex-start;gap:12px;line-height:22px}
.copy-rule{position:absolute;left:110px;top:2858px;width:978px;height:1px;background:var(--line)}
.copy{position:absolute;left:0;width:1200px;top:2876px;text-align:center;font-size:13px;color:var(--ink)}
.to-top{position:absolute;left:1123px;top:2836px;width:44px;height:44px;border-radius:50%;background:var(--teal)}
</style>
</head>
<body>

<header class="site-header">
  <div class="brand"><span class="dot"></span>KORVATH</div>
  <nav class="nav">
    <a class="active" style="left:416px">HOME</a>
    <a style="left:495px">ABOUT</a>
    <a style="left:581px">CONTACT</a>
    <a style="left:685px">OUR SERVICES</a>
    <a style="left:821px">NEWS/BLOGS</a>
  </nav>
  <div class="btn" style="left:929px;top:10px;width:158px;height:46px">Contact us</div>
</header>

<section class="hero" role="img" aria-label="Aerial night view of a container ship docked beside stacked shipping containers">
  <h1>E_COMMERCE &amp;<br>ORDER PORTALS</h1>
  <div class="btn">Read more</div>
  <div class="hero-arrow" style="left:32px">
    <svg width="50" height="50" viewBox="0 0 50 50"><path d="M35 25H15M23 17l-8 8 8 8" fill="none" stroke="#fff" stroke-width="2.5" stroke-linecap="round" stroke-linejoin="round"/></svg>
  </div>
  <div class="hero-arrow" style="left:1113px">
    <svg width="50" height="50" viewBox="0 0 50 50"><path d="M15 25h20M27 17l8 8-8 8" fill="none" stroke="#fff" stroke-width="2.5" stroke-linecap="round" stroke-linejoin="round"/></svg>
  </div>
  <div class="hero-dots"><span class="on" style="left:112px"></span><span style="left:134px"></span><span style="left:156px"></span></div>
</section>

<section class="services">
  <article class="service" style="left:55px">
    <svg width="80" height="80" viewBox="0 0 80 80"><circle cx="40" cy="40" r="30" fill="none" stroke="#2f9b3b" stroke-width="10" stroke-dasharray="8 6"/><circle cx="40" cy="40" r="24" fill="#2f9b3b" stroke="#222" stroke-width="2"/><circle cx="40" cy="40" r="17" fill="#fff" stroke="#222" stroke-width="2"/><path d="M31 35l9-5 9 5v11l-9 5-9-5zM31 35l9 5 9-5M40 40v11" fill="none" stroke="#222" stroke-width="2" stroke-linejoin="round"/></svg>
    <h3>PRODUCT<br>DEVELOPMENT</h3>
    <p>Increase turnover through automated order processes</p>
  </article>
  <article class="service" style="left:277px">
    <svg width="80" height="80" viewBox="0 0 80 80"><path d="M24 48l-8 18 10-2 5 8 8-18M56 48l8 18-10-2-5 8-8-18" fill="#2f9b3b" stroke="#222" stroke-width="2" stroke-linejoin="round"/><circle cx="40" cy="34" r="24" fill="#fff" stroke="#222" stroke-width="2.5"/><circle cx="40" cy="34" r="16" fill="#2c5b6b" stroke="#222" stroke-width="2"/><path d="M40 23l3.3 6.8 7.4 1-5.4 5.2 1.3 7.4L40 40l-6.6 3.4 1.3-7.4-5.4-5.2 7.4-1z" fill="#2f9b3b" stroke="#222" stroke-width="1.5"/></svg>
    <h3>BRAND<br>DEVELOPMENT</h3>
    <p>Assembly &amp; Fine-grained distribution on a project basis</p>
  </article>
  <article class="service" style="left:498px">
    <svg width="80" height="80" viewBox="0 0 80 80"><rect x="10" y="16" width="58" height="40" rx="3" fill="#fff" stroke="#222" stroke-width="2.5"/><rect x="6" y="56" width="66" height="6" rx="2" fill="#2f9b3b" stroke="#222" stroke-width="2"/><circle cx="36" cy="32" r="6" fill="#2f9b3b" stroke="#222" stroke-width="2"/><path d="M26 50c1-7 5-10 10-10s9 3 10 10" fill="#2c5b6b" stroke="#222" stroke-width="2"/><rect x="50" y="12" width="22" height="16" rx="3" fill="#fff" stroke="#222" stroke-width="2"/><path d="M55 20h12" stroke="#2f9b3b" stroke-width="2"/></svg>
    <h3>ONLINE<br>POSITIONING</h3>
    <p>Storage, Order Processing &amp; Shipping</p>
  </article>
  <article class="service" style="left:721px">
    <svg width="80" height="80" viewBox="0 0 80 80"><path d="M6 20h14" stroke="#2f9b3b" stroke-width="3"/><rect x="4" y="24" width="44" height="30" fill="#fff" stroke="#222" stroke-width="2.5"/><path d="M48 32h14l10 12v10H48z" fill="#2c5b6b" stroke="#222" stroke-width="2.5" stroke-linejoin="round"/><path d="M53 36h8l6 8H53z" fill="#fff" stroke="#222" stroke-width="1.5"/><circle cx="18" cy="58" r="6" fill="#fff" stroke="#222" stroke-width="2.5"/><circle cx="60" cy="58" r="6" fill="#2f9b3b" stroke="#222" stroke-width="2.5"/></svg>
    <h3>LOGISTICS &amp;<br>AFTERSALES</h3>
    <p>Setting up &amp; managing<br>Loyalty programs</p>
  </article>
  <article class="service" style="left:938px">
    <svg width="80" height="80" viewBox="0 0 80 80"><path d="M12 46l34-26 8 24z" fill="#fff" stroke="#222" stroke-width="2.5" stroke-linejoin="round"/><path d="M12 46l8 10 6-4" fill="#2c5b6b" stroke="#222" stroke-width="2.5" stroke-linejoin="round"/><path d="M22 52l6 12 7-3-4-11" fill="#fff" stroke="#222" stroke-width="2.5" stroke-linejoin="round"/><ellipse cx="50" cy="32" rx="5" ry="13" transform="rotate(-35 50 32)" fill="#2f9b3b" stroke="#222" stroke-width="2"/><path d="M60 14l4-6M64 24l8-2M58 8l1-4" stroke="#2f9b3b" stroke-width="3" stroke-linecap="round"/></svg>
    <h3>PROMOTIONAL<br>BBQS</h3>
    <p>Setting up &amp; managing<br>Loyalty programs</p>
  </article>
</section>

<section class="special">
  <h2>WHAT MAKES US SPECIAL</h2>
  <p>We believe that the partners we work for should be able to focus on building their brand and product. Korvath Supply therefore takes care of the process from order processing to delivery. Together with our Partner Korvath Promotional, we can also provide support in the commercial process. We have supplier relationships in more than 30 countries in both the retail and promotional products market.</p>
  <div class="btn">Read more</div>
  <div class="special-photo" role="img" aria-label="Shipping container being lifted onto a truck beside stacked coloured containers"></div>
</section>

<section class="silent">
  <h2>KORVATH SUPPLY ENSURES SILENT DISTRIBUTION</h2>
  <p>ensures the smooth distribution of promotional merchandise products for its customers. With our own warehouse and fleet, we are able to get products to the right place quickly and reliably, from small orders to larger, complex deliveries to multiple addresses.</p>
  <div class="btn">Ask for the possiblilities</div>
</section>

<section class="contact" role="img" aria-label="Dimmed photo of port cranes and stacked containers behind the contact form">
  <h2>CONTACT US ABOUT YOUR PROJECT</h2>
  <p class="lead">Would you like to speak to one of our specialists by telephone? Enter your details and we will contact you as soon as possible.</p>
  <div class="field" style="left:277px;top:206px;width:314px">
    <svg width="14" height="16" viewBox="0 0 14 16"><circle cx="7" cy="4" r="3.5" fill="#2c5b6b"/><path d="M0 16c0-5 3-7 7-7s7 2 7 7z" fill="#2c5b6b"/></svg>First Name</div>
  <div class="field" style="left:607px;top:206px;width:315px">
    <svg width="14" height="16" viewBox="0 0 14 16"><circle cx="7" cy="4" r="3.5" fill="#2c5b6b"/><path d="M0 16c0-5 3-7 7-7s7 2 7 7z" fill="#2c5b6b"/></svg>Company Name</div>
  <div class="field" style="left:277px;top:267px;width:314px">
    <svg width="18" height="14" viewBox="0 0 18 14"><rect x="1" y="1" width="16" height="12" fill="none" stroke="#2c5b6b" stroke-width="1.5"/><path d="M1 1l8 7 8-7" fill="none" stroke="#2c5b6b" stroke-width="1.5"/></svg>Email</div>
  <div class="field" style="left:607px;top:267px;width:315px">
    <svg width="16" height="16" viewBox="0 0 16 16"><path d="M3 1l3 3-2 2c1 2 3 4 6 6l2-2 3 3-2 2C7 15 1 9 1 3z" fill="#2c5b6b"/></svg>Phone</div>
  <div class="field area" style="left:277px;top:329px;width:645px">
    <svg width="18" height="14" viewBox="0 0 18 14" style="margin-top:3px"><rect x="1" y="1" width="16" height="12" fill="none" stroke="#2c5b6b" stroke-width="1.5"/><path d="M1 1l8 7 8-7" fill="none" stroke="#2c5b6b" stroke-width="1.5"/></svg>Enter Your message</div>
  <div class="btn">Request without obligation</div>
</section>

<footer class="site-footer">
  <div class="brand"><span class="dot"></span>KORVATH</div>

  <div class="foot-col">
    <h4 style="left:451px">QUICK LINKS</h4><div class="rule" style="left:453px"></div>
    <ul>
      <li style="left:453px;top:2670px">HOME</li>
      <li style="left:453px;top:2696px">OUR SERVICES</li>
      <li style="left:453px;top:2722px">ABOUT US</li>
      <li style="left:453px;top:2748px">OUR TEAM</li>
      <li style="left:453px;top:2774px">BLOG</li>
      <li style="left:453px;top:2800px">GALLERY</li>
    </ul>
  </div>
  <div class="foot-col">
    <h4 style="left:630px">LINKS</h4><div class="rule" style="left:632px"></div>
    <ul>
      <li style="left:632px;top:2670px">CONTACT</li>
      <li style="left:632px;top:2696px">SERVICES</li>
      <li style="left:632px;top:2722px">HOME</li>
      <li style="left:632px;top:2748px">OUR METHOD</li>
    </ul>
  </div>
  <div class="foot-col foot-contact">
    <h4 style="left:781px">CONTACT US</h4><div class="rule" style="left:783px"></div>
    <ul>
      <li style="left:783px;top:2668px">
        <svg width="18" height="22" viewBox="0 0 18 22"><path d="M9 1a8 8 0 0 0-8 8c0 6 8 12 8 12s8-6 8-12a8 8 0 0 0-8-8z" fill="#2c5b6b"/><circle cx="9" cy="9" r="3" fill="#fff"/></svg>
        <span>LINDENKADE 12,<br>5504 AB VELDHOVEN</span></li>
      <li style="left:783px;top:2727px">
        <svg width="18" height="18" viewBox="0 0 16 16"><path d="M3 1l3 3-2 2c1 2 3 4 6 6l2-2 3 3-2 2C7 15 1 9 1 3z" fill="#2c5b6b"/></svg>
        <span>VELDHOVEN OFFICE: +31 (0)10 555 0142</span></li>
      <li style="left:783px;top:2762px">
        <svg width="20" height="16" viewBox="0 0 18 14"><rect x="1" y="1" width="16" height="12" fill="none" stroke="#2c5b6b" stroke-width="1.5"/><path d="M1 1l8 7 8-7" fill="none" stroke="#2c5b6b" stroke-width="1.5"/></svg>
        <span>INFO@KORVATHSUPPLY.EXAMPLE</span></li>
      <li style="left:783px;top:2796px">
        <svg width="20" height="20" viewBox="0 0 20 20"><circle cx="10" cy="10" r="8.5" fill="none" stroke="#2c5b6b" stroke-width="1.5"/><path d="M10 5v5l-3 3" fill="none" stroke="#2c5b6b" stroke-width="1.5"/></svg>
        <span>09:00 – 18:00</span></li>
    </ul>
  </div>

  <div class="copy-rule"></div>
  <p class="copy">2021 Copyright © Korvath Supply</p>
  <div class="to-top">
    <svg width="44" height="44" viewBox="0 0 44 44"><path d="M18 24l4-4 4 4" fill="none" stroke="#fff" stroke-width="1.8" stroke-linecap="round" stroke-linejoin="round"/></svg>
  </div>
</footer>

</body>
</html>
```